KDWB Business Card

Looking for a business card design to incorporate our branding. We want to only use the colors listing in the Branding Package (attached).
Updates

Target Market(s)

People who need their phone or device fixed.

Industry/Entity Type

Electronics

Contact Information for Business Card

Please use:

Brightwick Gadget Clinic LLC
4810 E Harlow Ridge Rd
Suite 417
San Antonio, TX 78163

Marcus Delgrove, Store Manager

(210) 555-0147

Requirements
Must have
• Must include the colors that are contained within the Branding Package PDF file.

```html
<!DOCTYPE html>
<html lang="en">
<head>
<meta charset="utf-8">
<title>Brightwick Gadget Clinic – Business Card</title>
<link href="https://fonts.googleapis.com/css2?family=Questrial&display=swap" rel="stylesheet">
<style>
  :root {
    --brand-orange: #f0562a;
    --ink-grey: #4a4a4a;
    --rule-grey: #55585c;
    --paper: #ffffff;
    --backdrop: #2b2b2d;
  }
  html, body {
    margin: 0;
    padding: 0;
    width: 1200px;
    height: 880px;
    overflow: hidden;
    background: var(--backdrop);
    font-family: "Questrial", "Helvetica Neue", Arial, sans-serif;
  }
  .canvas {
    position: relative;
    width: 1200px;
    height: 880px;
  }
  .card {
    position: absolute;
    width: 600px;
    height: 343px;
    border-radius: 22px;
    overflow: hidden;
    box-shadow: 0 14px 30px rgba(0,0,0,0.45);
  }
  .card--front {
    left: 60px;
    top: 80px;
    background: var(--brand-orange);
    color: var(--paper);
  }
  .card--back {
    left: 540px;
    top: 457px;
    background: var(--paper);
  }
  .brand {
    position: absolute;
    display: flex;
    align-items: center;
    gap: 14px;
  }
  .brand__mark {
    border-radius: 10px;
    flex: none;
  }
  .brand__name {
    line-height: 1.05;
  }
  .card--front .brand {
    left: 110px;
    top: 112px;
  }
  .card--front .brand__mark {
    width: 62px;
    height: 62px;
    background: var(--paper);
  }
  .card--front .brand__name {
    font-size: 38px;
    color: var(--paper);
  }
  .legal-name {
    position: absolute;
    left: 0;
    right: 0;
    top: 218px;
    text-align: center;
    font-size: 17px;
    letter-spacing: 0.5px;
  }
  .card--back .brand {
    left: 36px;
    top: 138px;
    gap: 10px;
  }
  .card--back .brand__mark {
    width: 40px;
    height: 40px;
    background: var(--brand-orange);
    border-radius: 8px;
  }
  .card--back .brand__name {
    font-size: 22px;
    color: var(--brand-orange);
  }
  .divider {
    position: absolute;
    left: 330px;
    top: 50px;
    width: 1px;
    height: 170px;
    background: var(--brand-orange);
  }
  .contact {
    position: absolute;
    left: 355px;
    top: 36px;
    color: var(--ink-grey);
  }
  .contact__name {
    margin: 0;
    font-size: 22px;
    font-weight: 400;
    color: var(--brand-orange);
  }
  .contact__title {
    margin: 2px 0 20px;
    font-size: 14px;
  }
  .contact__address {
    font-style: normal;
    font-size: 15px;
    line-height: 1.35;
  }
  .contact__phone {
    display: flex;
    align-items: center;
    gap: 8px;
    margin-top: 18px;
    font-size: 15px;
  }
  .contact__phone svg {
    width: 20px;
    height: 20px;
  }
  .wave {
    position: absolute;
    left: 0;
    top: 0;
    width: 600px;
    height: 343px;
  }
</style>
</head>
<body>
<main class="canvas">

  <section class="card card--front" aria-label="Card front">
    <div class="brand">
      <span class="brand__mark"></span>
      <span class="brand__name">Brightwick<br>Gadget Clinic</span>
    </div>
    <p class="legal-name">Brightwick Gadget Clinic LLC</p>
  </section>

  <section class="card card--back" aria-label="Card back">
    <svg class="wave" viewBox="0 0 600 343" aria-hidden="true">
      <path d="M0,318 C220,332 430,300 600,215 L600,343 L0,343 Z" fill="var(--brand-orange)"/>
      <path d="M0,304 C220,318 430,286 600,200" fill="none" stroke="var(--rule-grey)" stroke-width="6"/>
    </svg>

    <div class="brand">
      <span class="brand__mark"></span>
      <span class="brand__name">Brightwick Gadget Clinic</span>
    </div>

    <div class="divider"></div>

    <div class="contact">
      <h1 class="contact__name">Marcus Delgrove</h1>
      <p class="contact__title">Store Manager</p>
      <address class="contact__address">
        4810 E Harlow Ridge Rd<br>
        Suite 417<br>
        San Antonio, TX 78163
      </address>
      <div class="contact__phone">
        <svg viewBox="0 0 20 20" aria-hidden="true">
          <rect width="20" height="20" rx="3" fill="var(--brand-orange)"/>
          <path d="M4,8 C4,5 16,5 16,8 L14,9.5 L12.5,7.8 L7.5,7.8 L6,9.5 Z" fill="#fff"/>
          <rect x="5.5" y="10" width="9" height="5.5" rx="1" fill="#fff"/>
        </svg>
        <span>(210) 555-0147</span>
      </div>
    </div>
  </section>

</main>
</body>
</html>
```